Verodex business card

Business card for sustainable investment company called "Verodex". Verodex is an exchange platform selling carbon credits between buyers and sellers. Carbon Credits are an environmental commodity for reducing global carbon emissions.

the card should obviously have our logo and the theme should be sustainability/environment mixed with a trading platform.

Contact Information for Business Card

Logo, Name, Title, Phone, Email

Colors
0054AA
0677BA
7BADD7
CADEEF
E8F1F8
0094D4
00A9DD
6FCCEA
C7EBF8
E9F6FB
00AB8E
00BBA5
67D7C9
C6EFE9
E9F9F6
59FF00
82FF00
B8FF75
E3FFCB
F4FFEA

```html
<!DOCTYPE html>
<html lang="en">
<head>
<meta charset="utf-8">
<title>Verodex business card</title>
<link href="https://fonts.googleapis.com/css2?family=Montserrat:wght@400;500;600;700&display=swap" rel="stylesheet">
<style>
  :root {
    --navy: #15295a;
    --navy-deep: #11224b;
    --sky: #2fb4e6;
    --sky-light: #62cde6;
    --blue: #3f7fd0;
    --ink: #1c2333;
    --paper: #ffffff;
    --backdrop: #e4e7ec;
  }
  * { margin: 0; padding: 0; box-sizing: border-box; }
  html, body {
    width: 1200px; height: 900px; overflow: hidden;
    background: var(--backdrop);
    font-family: "Montserrat", sans-serif;
  }
  .canvas { position: relative; width: 1200px; height: 900px; }
  .card {
    position: absolute; width: 700px; height: 400px;
    box-shadow: 0 10px 28px rgba(20, 30, 50, 0.22);
    overflow: hidden;
  }
  .card-front { left: 110px; top: 40px; background: var(--navy); }
  .card-back { left: 390px; top: 460px; background: var(--paper); }

  .brand { position: absolute; display: flex; align-items: center; gap: 22px; }
  .brand-dot { width: 62px; height: 62px; border-radius: 50%; }
  .brand-name { font-weight: 700; letter-spacing: 2px; line-height: 1; }

  .card-front .brand { left: 50%; top: 50%; transform: translate(-50%, -50%); }
  .card-front .brand-dot { background: var(--sky); }
  .card-front .brand-name { color: var(--paper); font-size: 66px; }

  .card-back .brand { left: 150px; top: 64px; gap: 20px; }
  .card-back .brand-dot { width: 54px; height: 54px; background: var(--sky); }
  .card-back .brand-name { color: var(--navy); font-size: 58px; }

  .swoosh { position: absolute; inset: 0; width: 700px; height: 400px; }

  .details { position: absolute; left: 150px; top: 160px; display: flex; align-items: stretch; }
  .person { text-align: right; padding-right: 20px; padding-top: 18px; }
  .person-name { font-weight: 700; font-size: 25px; letter-spacing: 0.5px; }
  .person-name .first { color: var(--sky); }
  .person-name .last { color: var(--navy); }
  .person-title { font-size: 17px; color: var(--ink); margin-top: 2px; }
  .divider { width: 1.5px; background: var(--sky); }
  .contact { list-style: none; padding-left: 18px; }
  .contact li {
    display: flex; align-items: center; gap: 10px;
    font-size: 17px; color: var(--ink); height: 30px;
  }
  .contact svg { width: 17px; height: 17px; flex: none; }
</style>
</head>
<body>
<main class="canvas">
  <section class="card card-front">
    <div class="brand">
      <span class="brand-dot"></span>
      <span class="brand-name">VERODEX</span>
    </div>
  </section>

  <section class="card card-back">
    <svg class="swoosh" viewBox="0 0 700 400" aria-hidden="true">
      <defs>
        <linearGradient id="swoosh-line" x1="0" y1="1" x2="1" y2="0">
          <stop offset="0" stop-color="#62cde6"/>
          <stop offset="0.5" stop-color="#2fb4e6"/>
          <stop offset="1" stop-color="#3f6fc8"/>
        </linearGradient>
      </defs>
      <path d="M700 120 C 650 260, 470 350, 150 400 L 700 400 Z" fill="var(--navy)"/>
      <path d="M660 150 C 610 270, 430 340, 130 384" fill="none" stroke="url(#swoosh-line)" stroke-width="9" stroke-linecap="round"/>
    </svg>

    <div class="brand">
      <span class="brand-dot"></span>
      <span class="brand-name">VERODEX</span>
    </div>

    <div class="details">
      <div class="person">
        <p class="person-name"><span class="first">DANIEL</span> <span class="last">MARSH</span></p>
        <p class="person-title">Co-Founder</p>
      </div>
      <span class="divider"></span>
      <ul class="contact">
        <li>
          <svg viewBox="0 0 24 24"><path fill="#2fb4e6" d="M6.6 10.8a15.1 15.1 0 0 0 6.6 6.6l2.2-2.2a1 1 0 0 1 1-.25 11.4 11.4 0 0 0 3.6.57 1 1 0 0 1 1 1V20a1 1 0 0 1-1 1A17 17 0 0 1 3 4a1 1 0 0 1 1-1h3.5a1 1 0 0 1 1 1c0 1.25.2 2.45.57 3.57a1 1 0 0 1-.25 1z"/></svg>
          555-210-4378
        </li>
        <li>
          <svg viewBox="0 0 24 24"><rect x="2" y="5" width="20" height="14" rx="2" fill="#2fb4e6"/><path d="M3 6l9 7 9-7" fill="none" stroke="#fff" stroke-width="1.8"/></svg>
          info@verodex.com
        </li>
        <li>
          <svg viewBox="0 0 24 24"><circle cx="12" cy="12" r="10" fill="#2fb4e6"/><path d="M2 12h20M12 2c3 3 3 17 0 20M12 2c-3 3-3 17 0 20" fill="none" stroke="#fff" stroke-width="1.4"/></svg>
          www.verodex.com
        </li>
      </ul>
    </div>
  </section>
</main>
</body>
</html>
```